Cosmetic Dental Advert For lift in busy CBD

We need a DIRECT RESPONSE advert designed for a cosmetic dentist that is placing adverts into a building lift.

OFFICE PROVIDES BRANDS ACCESS TO REACH HIGH INCOME PROFESSIONALS WITHIN PREMIUM BUSINESS ENVIRONMENTS

We are not advertising a specific clinic so we want people to go to the website that is advertised and ask for the free initial consultation.

You can reduce the amount of words / points to make it simpler to read.

Target Market(s)

Professional at work - seeing advert in a lift or foyer

Industry/Entity Type

Dental

Colors

Designer to choose colors to be used in the design.

Requirements
Must have
• The domain "www.grinvale47.com.au" must be very strong and encourage people to visit / search for it.
• The offer is a ["FREE Initial consultation" with voucher code "grinvale47"]
• The advert must be in Vector format.
• Apply the landing page corner image bottom right
Nice to have
• Provide a Male / Female version
• Emphasize the beautiful smile like in the sample
Should not have
• Must not be busy. This is a direct response so the viewer must get the call to action in 2 seconds

```html
<!DOCTYPE html>
<html lang="en">
<head>
<meta charset="utf-8">
<title>Transform your smile – Cosmetic Dentistry</title>
<link href="https://fonts.googleapis.com/css2?family=Roboto:wght@300;400;700&display=swap" rel="stylesheet">
<style>
  :root {
    --paper: #ffffff;
    --plus: #d9d9de;
    --pink: #e0198c;
    --pink-soft: #e04fb4;
    --pink-deep: #b8106f;
    --navy: #2e3190;
    --navy-dark: #23266f;
    --white: #ffffff;
    --curl: #eeeeef;
    --curl-shade: #c9c9cd;
  }
  html, body { margin: 0; padding: 0; overflow: hidden; }
  body { background: var(--paper); }
  .poster {
    position: relative;
    width: 923px; height: 1200px;
    overflow: hidden;
    background: var(--paper);
    font-family: "Roboto", Arial, sans-serif;
  }
  .poster > svg { position: absolute; left: 0; top: 0; }
  .headline { position: absolute; left: 0; top: 0; width: 923px; margin: 0; font-weight: 300; }
  .headline span { position: absolute; white-space: nowrap; line-height: 1; }
  .headline .lead { color: var(--navy); font-size: 70px; }
  .headline .lead-1 { left: 325px; top: 112px; }
  .headline .lead-2 { left: 340px; top: 194px; }
  .headline .key { color: var(--white); font-size: 150px; left: 420px; top: 340px; letter-spacing: -3px; font-weight: 400; }
  .headline .sub { color: var(--pink); font-size: 72px; left: 510px; }
  .headline .sub-1 { top: 478px; left: 600px; }
  .headline .sub-2 { top: 556px; left: 512px; }
  .headline .sub-3 { top: 634px; left: 545px; }
  .portrait {
    position: absolute; left: 0; top: 220px; width: 520px; height: 900px;
    background: linear-gradient(180deg, #c79a86 0%, #6b4b40 40%, #2b2b30 75%, #1c1c22 100%);
    border-radius: 240px 240px 0 0;
  }
  .offer { position: absolute; left: 28px; top: 948px; width: 650px; text-align: center; color: var(--white); }
  .offer-title { margin: 0; font-size: 52px; font-weight: 700; line-height: 1.05; }
  .offer-code { margin: 4px 0 0; font-size: 35px; font-weight: 400; }
  .web-bar {
    position: absolute; left: 0; top: 1122px; width: 640px; height: 78px;
    background: var(--navy); border-radius: 0 10px 0 0;
    display: flex; align-items: center; justify-content: center;
    color: var(--white); font-size: 50px; font-weight: 700; text-decoration: none;
  }
  .brand { position: absolute; left: 740px; top: 1134px; color: var(--navy); }
  .brand-name { display: flex; align-items: center; gap: 8px; font-size: 36px; font-weight: 700; line-height: 1; }
  .brand-dot { width: 14px; height: 14px; border-radius: 50%; background: var(--navy); }
  .brand-tag { margin-top: 4px; font-size: 12px; font-weight: 400; letter-spacing: 1px; text-transform: uppercase; }
</style>
</head>
<body>
<main class="poster">
  <svg width="923" height="1200" viewBox="0 0 923 1200" aria-hidden="true">
    <g class="plus-marks" stroke="var(--plus)" stroke-width="8">
      <path d="M180 140h60M210 110v60"/>
      <path d="M45 60h40M65 40v40"/>
      <path d="M775 150h44M797 128v44"/>
      <path d="M860 60h56M888 32v56"/>
      <path d="M745 800h60M775 770v60"/>
      <path d="M720 1000h40M740 980v40"/>
      <path d="M90 170h30M105 155v30"/>
    </g>
    <circle class="circle-pink" cx="462" cy="190" r="215" fill="var(--pink-soft)"/>
    <circle class="circle-navy" cx="680" cy="520" r="285" fill="var(--navy)"/>
  </svg>

  <div class="portrait" role="img" aria-label="Smiling professional woman in a dark blazer with arms crossed"></div>

  <h1 class="headline">
    <span class="lead lead-1">Transform</span>
    <span class="lead lead-2">your</span>
    <span class="key">smile</span>
    <span class="sub sub-1">with</span>
    <span class="sub sub-2">Cosmetic</span>
    <span class="sub sub-3">Dentistry</span>
  </h1>

  <svg width="923" height="1200" viewBox="0 0 923 1200" aria-hidden="true">
    <g class="page-curl">
      <path d="M923 960 L923 1135 L730 1135 Q840 1100 923 960Z" fill="var(--curl-shade)"/>
      <path d="M923 960 Q860 1030 730 1135 Q800 1050 820 980 Q870 990 923 960Z" fill="var(--curl)"/>
    </g>
    <g class="offer-ribbon">
      <path d="M630 905 L660 880 L668 1000 L630 1000Z" fill="var(--pink-deep)"/>
      <path d="M70 1040 L200 1040 L175 1120 L130 1080Z" fill="var(--pink-deep)"/>
      <rect x="20" y="935" width="670" height="120" fill="var(--pink)"/>
    </g>
  </svg>

  <div class="offer">
    <p class="offer-title">Free initial consultation</p>
    <p class="offer-code">Voucher code “grinvale47”</p>
  </div>

  <a class="web-bar" href="#">www.grinvale47.com.au</a>

  <div class="brand">
    <div class="brand-name"><span class="brand-dot"></span>Dentavia</div>
    <div class="brand-tag">dental care network</div>
  </div>
</main>
</body>
</html>
```